Contemporary woman's fiction set in New Zealand

Cover design for my contemporary novel "Mending Lorna"
The title of the book works on two levels - Lorna as a teacher, and someone (Bram) teaching her that she needs to overcome hurtful experiences in the past in order to be able to trust and love again (see synopsis below)

Requirements:
Book Title: Mending Lorna
Author name: Carla Voskuil
Font: Clean, strong fonts - nothing frilly or cursive

Target audience: Women 25+

Book cover:
Should be eye-catching and convey strong emotion
Close up shot or portrait of Lorna: 30 year old, slim/small build, green eyes, curly dark hair (past shoulders). Wearing a dark greenstone/pounamu pendant (rau kumara twist) on a dark waxed cord sitting just below her collarbone. She could be wearing a snug-ftting green long-sleeved top, but not a necessity.

Her look should be a mixture of being wary and challenging as if she asked "So what it is that you are trying to teach me?” or “I’m trying really hard to grasp what you are teaching me, but I can’t/won’t follow”.
Her look should reflect the ambivalent feelings that she is going through – she really wants to believe that Bram is a good guy whom she can trust, but experiences in her past have made her very distrustful.

Alternatively, her look could be more relaxed. Not a full-blown smile, but a more upbeat emotion.
Whether she is smiling or not is not the most important part. Crucial is that strong emotions should be conveyed through her look.

In the background I would like to see the landscape of Central Otago/NZ - see attached pictures and pixmoorly pictures 82014635 & 51709324 as reference.

I have also attached a picture of the above mentioned greenstone pendant.

Cover design should be for both Bexlo and other ebook formats.
For Bexlo, cover art has an ideal height/width ratio of 1.6, this means:
• A minimum of 625 pixels on the shortest side and 1000 pixels on the longest side
• For best quality, image would be 1563 pixels on the shortest side and 2500 pixels on the longest side
Must include all files for printed book cover and ebook cover

Synopsis
Lorna has put up with Malcolm’s bullying for so long, she is surprised when Bram, a visiting adviser to her school, turns into an ally she doesn’t really want. Fiercely independent and wary of people (except for children, of course), she is perfectly capable of dealing with Malcolm by herself.
Despite her efforts to keep Bram at an arm’s length, he manages to gain her trust, and a tender relationship starts to form. A future with Bram looks certain until a misunderstanding leads Lorna to pull away from him. When she recognises her mistake, it is too late to win him back.
The breakup affects her greatly, down to the one constant she could always fall back on in times of crisis: her love of teaching. Lorna fails to meet her own high expectations of an inspiring teacher which leads her onto a downward spiral of feelings of inadequacy and guilt.
After weeks of misery, Lorna takes to the hills of Central Otago to clear her head. High up in the tussock country she loves so much, she realises that it is time to move on and let go of the past.
The decision comes as a relief, but a sudden weather change gives Lorna little time to dwell on it.
Will Lorna make it home safely to put her decisions into action? And will Bram ever find out what happened to her?

Thank you for the designs submitted so far. I have purchased images from pixmoorly to use for the cover.

Use any of the three pictures of the young woman, and if possible, photoshop/overlay one of the landscape pictures.
I also wondered if the girl's eyes can be changed to green?

Thank you for all designs submitted so far. As previously mentioned, I have uploaded some pictures that you may want to use. Please feel free to omit the greenstone pendant as it it may look odd or out of place.

```html
<!DOCTYPE html>
<html lang="en">
<head>
<meta charset="utf-8">
<title>Mending Lorna — Cover Wrap</title>
<link rel="stylesheet" href="https://fonts.googleapis.com/css2?family=Josefin+Sans:wght@300;400&family=Fira+Sans:wght@400&display=swap">
<style>
  :root {
    --canvas: #f4f4f2;
    --band-red: #d93a2b;
    --paper-white: #ffffff;
    --sky-pale: #e9ece6;
    --hill-gold: #c9a15c;
    --hill-shadow: #a77e3e;
    --grass-gold: #b98a3a;
    --grass-deep: #8a5e24;
    --portrait-warm: #b07a4a;
  }
  * { box-sizing: border-box; margin: 0; padding: 0; }
  html, body {
    width: 1200px; height: 851px; overflow: hidden;
    background: var(--canvas);
  }
  .cover-wrap {
    position: absolute; left: 175px; top: 105px;
    width: 850px; height: 640px;
    display: flex;
    box-shadow: 0 12px 40px rgba(0,0,0,0.12);
  }
  .back-cover, .front-cover { position: relative; width: 400px; height: 640px; overflow: hidden; }
  .spine { position: relative; width: 50px; height: 640px; background: var(--band-red); }

  .landscape {
    position: absolute; inset: 0;
    background: linear-gradient(180deg,
      var(--sky-pale) 0%, var(--sky-pale) 8%,
      var(--hill-gold) 16%, var(--hill-shadow) 26%,
      var(--hill-gold) 36%, var(--grass-gold) 60%,
      var(--grass-deep) 100%);
  }
  .portrait {
    position: absolute; left: 40px; right: 0; top: 330px; bottom: 0;
    background: radial-gradient(ellipse at 40% 45%, var(--portrait-warm) 0%, var(--grass-gold) 55%, transparent 80%);
  }

  .title-band {
    position: absolute; left: 0; right: 0;
    background: var(--band-red);
    color: var(--paper-white);
    font-family: "Josefin Sans", sans-serif;
    font-weight: 300;
    text-transform: uppercase;
  }
  .title-line { font-weight: 300; white-space: nowrap; }

  .front-cover .title-band { top: 180px; height: 150px; padding: 16px 0 0 10px; }
  .front-cover .title-line { font-size: 68px; line-height: 0.95; letter-spacing: -1px; }
  .front-cover .title-row { display: flex; align-items: flex-start; gap: 12px; margin-top: 2px; }
  .author-name { font-size: 24px; line-height: 1.1; font-weight: 300; padding-top: 6px; white-space: nowrap; }

  .back-cover .title-band { top: 44px; height: 116px; display: flex; align-items: center; justify-content: center; }
  .back-cover .title-line { font-size: 40px; letter-spacing: -0.5px; }

  .blurb-box {
    position: absolute; left: 36px; right: 36px; top: 198px; height: 320px;
    background: var(--band-red);
    padding: 18px 20px;
    color: var(--paper-white);
    font-family: "Fira Sans", sans-serif;
    font-size: 15px; line-height: 1.3;
    text-align: justify;
  }
  .blurb-box p + p { margin-top: 16px; }

  .spine-title {
    position: absolute; top: 24px; left: 50%;
    transform: translateX(-50%);
    writing-mode: vertical-rl;
    color: var(--paper-white);
    font-family: "Josefin Sans", sans-serif;
    font-weight: 300; font-size: 32px; text-transform: uppercase;
    letter-spacing: -0.5px; white-space: nowrap;
  }
</style>
</head>
<body>
  <main class="cover-wrap">
    <section class="back-cover">
      <div class="landscape" role="img" aria-label="Central Otago tussock hills under a pale sky"></div>
      <div class="title-band"><h2 class="title-line">Mending Lorna</h2></div>
      <div class="blurb-box">
        <p>Lorem ipsum dolor sit amet, consetetur sadipscing elitr, sed diam nonumy eirmod tempor invidunt ut labore et dolore magna aliquyam erat, sed diam voluptua.</p>
        <p>At vero eos et accusam et justo duo dolores et ea rebum. Stet clita kasd gubergren, no sea takimata sanctus est Lorem ipsum dolor sit amet. Lorem ipsum dolor sit amet, consetetur sadipscing elitr, sed diam nonumy eirmod tempor invidunt ut labore et dolore magna aliquyam erat, sed diam voluptua.</p>
      </div>
    </section>
    <section class="spine">
      <span class="spine-title">Mending Lorna</span>
    </section>
    <section class="front-cover">
      <div class="landscape" role="img" aria-label="Golden hills of Central Otago beneath a hazy sky"></div>
      <div class="portrait" role="img" aria-label="Portrait of Lorna looking up, in a golden tussock field"></div>
      <div class="title-band">
        <h1 class="title-line">Mending</h1>
        <div class="title-row">
          <span class="title-line">Lorna</span>
          <span class="author-name">Carla<br>Voskuil</span>
        </div>
      </div>
    </section>
  </main>
</body>
</html>
```